ZESTORAMA Business Card Design

ZESTORAMA
Zestorama is a food van, serving high vibe delicious food to go. This business is dedicated to healthy delicious feel good food, beauty in service and a sustainable planet.

The van will operate in the south west of western Australia at music festivals events markets wherever people need great food to go!

I like the idea of vibrant green mixed with a yellow?? background with some rays like the sun through the background.
The font needs to say vibrant energetic
TO ME -vibrant energetic font has to appear to be on the move - perhaps with shading??

I like fusha if that works for font? but the colour has to say food too.

I would like a symbol on the card a simple V turned into a womans raised arms. This should be vibrant too.
Thank you
Blessings
Marisol

Target Market(s)

target lovers of healthy high vibe food. music festival goers. age 18- 50 feel. audiance conscious eaters of feel great food

Industry/Entity Type

Events

Contact Information for Business Card

ZESTORAMA
High Vibe Food
Van
Marisol -owner/opperator
0471583906
Face book symbol - ZESTORAMA

on the I would like a logo of a simple V turned into a womans arms up toward the sky flip side

My number and name again
Zestorama- feel great mobile food
Festivals, events, markets & where high vibe food 2 go is appreciated

Requirements
Nice to have
• Moving energetic font
colour that says high vibe and healthy food

a logo that is a simple V turned into a woman's raised arms in gratitude

```html
<!DOCTYPE html>
<html lang="en">
<head>
<meta charset="utf-8">
<title>Zestorama Business Card</title>
<link rel="stylesheet" href="https://fonts.googleapis.com/css2?family=Michroma&display=swap">
<style>
  :root {
    --backdrop: #d4d5d7;
    --slate: #3e4451;
    --slate-light: #4b5261;
    --ink: #1d1d1f;
    --white: #ffffff;
    --green-deep: #17a33a;
    --green: #3cbf2f;
    --lime: #c9e62b;
    --tile-top: #7ad64a;
    --tile-bottom: #1f9a2e;
    --title-yellow: #e3f04a;
    --logo-green: #55c22b;
  }
  * { margin: 0; padding: 0; box-sizing: border-box; }
  html, body {
    width: 1200px; height: 861px; overflow: hidden;
    background: var(--backdrop);
    font-family: "Michroma", sans-serif;
  }
  .card {
    position: absolute; left: 140px; top: 168px;
    width: 920px; height: 526px;
    background: var(--slate);
    box-shadow: 0 18px 40px rgba(0,0,0,.35);
    overflow: hidden;
  }
  .name-bar {
    position: absolute; left: 0; top: 24px; width: 880px; height: 46px;
    background: linear-gradient(90deg, var(--green-deep), var(--green) 45%, var(--lime));
    display: flex; align-items: center; gap: 16px; padding-left: 34px;
  }
  .name-bar .person { color: var(--white); font-size: 20px; letter-spacing: 1px; }
  .name-bar .role { color: var(--title-yellow); font-size: 11px; }
  .links { position: absolute; left: 70px; top: 96px; display: flex; gap: 90px; }
  .link { width: 122px; display: flex; flex-direction: column; align-items: center; }
  .tile {
    width: 112px; height: 112px; border-radius: 8px;
    background: linear-gradient(180deg, var(--tile-top), var(--tile-bottom));
    border: 3px solid rgba(255,255,255,.25);
    display: flex; flex-direction: column; align-items: center; justify-content: center; gap: 10px;
    color: var(--white); font-size: 11px;
  }
  .tile .dot { width: 40px; height: 40px; border-radius: 50%; border: 3px solid var(--white); }
  .link .detail { margin-top: 12px; color: var(--white); font-size: 11px; line-height: 1.5; text-align: center; }
  .contacts {
    position: absolute; left: 70px; top: 292px; display: flex; gap: 40px;
    color: var(--white); font-size: 13px; align-items: center;
  }
  .contacts span { display: flex; align-items: center; gap: 8px; }
  .contacts svg { width: 16px; height: 16px; fill: var(--white); }
  .logo-band {
    position: absolute; left: 0; top: 330px; width: 860px; height: 196px;
    background: var(--ink);
    display: flex; align-items: center; justify-content: center;
  }
  .end-strip { position: absolute; left: 860px; top: 330px; width: 60px; height: 196px; background: var(--slate-light); }
  .brand { color: var(--logo-green); font-size: 56px; letter-spacing: 2px; }
</style>
</head>
<body>
  <div class="card">
    <div class="name-bar">
      <span class="person">MARISOL REYES</span>
      <span class="role">Managing Director</span>
    </div>

    <div class="links">
      <div class="link">
        <div class="tile">
          <svg width="44" height="40" viewBox="0 0 44 40"><path d="M22 2 2 20h6v18h10V26h8v12h10V20h6z" fill="#fff"/></svg>
          Address
        </div>
        <p class="detail">Your Address<br>City State zip</p>
      </div>
      <div class="link">
        <div class="tile"><span class="dot"></span>Feedbook</div>
        <p class="detail">feedbook.com<br>/zestorama</p>
      </div>
      <div class="link">
        <div class="tile"><span class="dot"></span>Chirper</div>
        <p class="detail">@zestorama</p>
      </div>
      <div class="link">
        <div class="tile"><span class="dot"></span>Linkpro</div>
        <p class="detail">Your Name</p>
      </div>
    </div>

    <div class="contacts">
      <span><svg viewBox="0 0 16 16"><path d="M3 1h3l1 4-2 1a9 9 0 0 0 5 5l1-2 4 1v3a2 2 0 0 1-2 2A13 13 0 0 1 1 3a2 2 0 0 1 2-2z"/></svg>0471 583 906</span>
      <span><svg viewBox="0 0 16 16"><path d="M1 3h14v10H1z M1 3l7 6 7-6" fill="none" stroke="#fff" stroke-width="1.6"/></svg>hello@zestorama.com</span>
      <span><svg viewBox="0 0 16 16"><circle cx="8" cy="8" r="6.5" fill="none" stroke="#fff" stroke-width="1.5"/><path d="M1.5 8h13M8 1.5c-3 3-3 10 0 13M8 1.5c3 3 3 10 0 13" fill="none" stroke="#fff" stroke-width="1.2"/></svg>www.zestorama.com</span>
    </div>

    <div class="logo-band">
      <span class="brand">Zestorama</span>
    </div>
    <div class="end-strip"></div>
  </div>
</body>
</html>
```